Advertising company unique advertising platform

we need a logo design for a new company based in Australia Melbourne. We develop innovated advertising platform where consumer can use this platform to get regular discount, as business owner they can use this platform for free advertisement. Payment for this advertisement platform only payable every two weeks, when I generate revenue for their business

Industry/Entity Type

Advertising

Contact Information for Business Card

Dale Morven | Co-Founder |Managing Director
Suite 718 240 Wattlebrook Lane Melbourne Vic 3000

ABN 38 614 207 923
Tel: +61 0487 259 318 | Email: dale.morven@plivorantu.com

Font styles to use
Decorative
Script

Requirements
Must have
• Try few different design and some round corner business card
Should not have
• One round corner business card...try 4 different colour background not only black, make sure two side is designed. Be creative so imagine you are giving this to a client make sure has wow factor, if you can also try one design with engrave like all the logo, words look 3d feel
• The word Advertising Platform use attached file font

```html
<!DOCTYPE html>
<html lang="en">
<head>
<meta charset="utf-8">
<title>Vantori Loop – Business Card</title>
<link href="https://fonts.googleapis.com/css2?family=Roboto:wght@400;500;700&display=swap" rel="stylesheet">
<style>
  :root {
    --bg: #e9e6e2;
    --card-dark: #29292b;
    --ink: #1f1f22;
    --brand: #f2692c;
    --warm-red: #e9482f;
    --warm-yellow: #f2c542;
    --teal: #19e3b1;
    --sky: #1cc6f2;
    --muted: #d9d9d9;
  }
  * { box-sizing: border-box; margin: 0; padding: 0; }
  html, body { width: 1200px; height: 886px; overflow: hidden; }
  body {
    background: var(--bg);
    font-family: "Roboto", Arial, sans-serif;
    display: flex;
    flex-direction: column;
    align-items: center;
    justify-content: center;
    gap: 40px;
  }
  .card {
    position: relative;
    width: 660px;
    height: 403px;
    border-radius: 26px;
    overflow: hidden;
    background: var(--card-dark);
    box-shadow: 0 10px 24px rgba(0,0,0,0.18);
  }

  /* Back side */
  .card-back .brand-lockup {
    position: absolute;
    left: 0; right: 0; top: 130px;
    display: flex;
    align-items: center;
    justify-content: center;
    gap: 18px;
  }
  .brand-mark {
    width: 70px; height: 70px;
    border-radius: 50%;
    background: var(--brand);
  }
  .brand-name {
    font-weight: 700;
    font-size: 50px;
    line-height: 1;
    color: var(--brand);
    letter-spacing: 1px;
  }
  .card-back .website {
    position: absolute;
    left: 0; right: 0; bottom: 56px;
    text-align: center;
    color: var(--muted);
    font-size: 16px;
    letter-spacing: 6px;
  }

  /* Front side */
  .card-front .band-warm {
    position: absolute;
    left: 0; right: 0; top: 118px; height: 178px;
    background: linear-gradient(90deg, var(--warm-red) 0%, #f08a36 30%, var(--warm-yellow) 55%, #f08a36 78%, var(--warm-red) 100%);
  }
  .card-front .band-dark-right {
    position: absolute;
    left: 500px; right: 0; top: 118px; height: 92px;
    background: var(--card-dark);
  }
  .card-front .band-cool {
    position: absolute;
    left: 0; right: 0; bottom: 0; height: 107px;
    background: linear-gradient(90deg, var(--teal) 0%, #6fb2e0 50%, var(--sky) 100%);
  }
  .card-front .brand-name {
    position: absolute;
    left: 34px; top: 36px;
    font-size: 46px;
  }
  .card-front .symbol-area {
    position: absolute;
    left: 448px; top: 66px;
    width: 160px; height: 160px;
    border-radius: 50%;
    background: var(--brand);
  }
  .contact {
    position: absolute;
    left: 34px; top: 132px;
    color: var(--ink);
  }
  .contact .person-name { font-size: 21px; font-weight: 700; }
  .contact .role { font-size: 16px; font-weight: 500; line-height: 1.2; }
  .contact .role:first-of-type { margin-top: 4px; }
  .contact .line {
    display: flex; align-items: center; gap: 10px;
    font-size: 16px; margin-top: 6px;
  }
  .contact .line svg { width: 14px; height: 14px; fill: var(--ink); }
  .contact .line:first-of-type { margin-top: 10px; }
  .company-block {
    position: absolute;
    left: 0; right: 0; bottom: 22px;
    text-align: center;
    color: var(--ink);
    font-size: 17px;
    line-height: 1.5;
  }
</style>
</head>
<body>
  <section class="card card-back">
    <div class="brand-lockup">
      <span class="brand-mark"></span>
      <span class="brand-name">Vantori Loop</span>
    </div>
    <p class="website">www.plivorantu.com</p>
  </section>

  <section class="card card-front">
    <div class="band-warm"></div>
    <div class="band-dark-right"></div>
    <div class="band-cool"></div>
    <span class="brand-name">Vantori Loop</span>
    <div class="symbol-area" role="img" aria-label="Brand symbol area"></div>
    <div class="contact">
      <p class="person-name">DALE MORVEN</p>
      <p class="role">CO-FOUNDER</p>
      <p class="role">MANAGING DIRECTOR</p>
      <p class="line">
        <svg viewBox="0 0 24 24" aria-hidden="true"><path d="M6.6 10.8a15.1 15.1 0 0 0 6.6 6.6l2.2-2.2a1 1 0 0 1 1-.25 11.4 11.4 0 0 0 3.6.57 1 1 0 0 1 1 1V20a1 1 0 0 1-1 1A17 17 0 0 1 3 4a1 1 0 0 1 1-1h3.5a1 1 0 0 1 1 1c0 1.25.2 2.450.57 3.57a1 1 0 0 1-.25 1z"/></svg>
        +61 0487 259 318
      </p>
      <p class="line">
        <svg viewBox="0 0 24 24" aria-hidden="true"><path d="M2 5h20v14H2z M2 5l10 8 10-8" fill="none" stroke="#1f1f22" stroke-width="2"/></svg>
        dale.morven@plivorantu.com
      </p>
    </div>
    <div class="company-block">
      <p>Plivorantu | ABN 38 614 207 923</p>
      <p>Suite 718 240 Wattlebrook Lane, Melbourne Vic 3000</p>
    </div>
  </section>
</body>
</html>
```